Distribution/Printing company needs a web site to inform prospective customers on what we do.

Distribution/Printing/Packaging company needs a web site to inform prospective customers on what we do. Please look at our direct to consumer web site (under development) for an idea of the product lines we sell: storedev.maplewickhaven.com
Logo files are attached as is a flyer that is under development which contains other information about the company (this is to be used for content- not to be posted as is). The web site should be focused on our business customer base and is not intended to be direct to consumer. Site should have a link to our consumer web site.
Site design should be mobile friendly, or mobile could be redirected to a mobile version. This web site will be strictly informational and will not be designed for any sales transactions.

Target Market(s)

Manufacturing and retail businesses, any other multi-site business that would benefit from centralized pricing and budget controls we can provide (banks, medical/dental offices, educational facilities, etc).

Industry/Entity Type

It Company

Coding

Coded - Design and coding required

Number of Pages Required

5+ page

Requirements
Must have
• 1) Top level menu: Products, about us, locations, contact us, news
• 2) page with news/promotions that is easily updated
• 3) "contact us" form (name, company, phone, email address) email link
• 4) link to www.store.maplewickhaven.com with information that lower pricing is available for businesses
• 5) SEO keywords
• 6) Link to powerpoint presentation file
Nice to have
• 1) our phone number should appear on every page near the top

```html
<!DOCTYPE html>
<html lang="en">
<head>
<meta charset="utf-8">
<title>Maplewick Haven Supply</title>
<link href="https://fonts.googleapis.com/css2?family=Open+Sans:wght@400;600;700&family=Roboto+Condensed:wght@700&display=swap" rel="stylesheet">
<style>
:root{
  --ink:#1d1d1d;
  --text:#333;
  --muted:#777;
  --line:#d9d9d9;
  --band:#efeff0;
  --accent:#f5c400;
  --price:#e2352a;
  --footer:#2b2b2b;
  --footer-text:#d6d6d6;
  --white:#fff;
}
*{box-sizing:border-box;margin:0;padding:0}
html,body{width:698px;height:1200px;overflow:hidden;background:var(--white)}
body{font-family:"Open Sans",Arial,sans-serif;color:var(--text);position:relative}
.site-header{position:absolute;top:0;left:0;width:698px;height:97px}
.brand{position:absolute;left:60px;top:54px;display:flex;align-items:center;gap:6px}
.brand-square{width:10px;height:10px;background:var(--ink)}
.brand-name{font-weight:700;font-size:12.5px;color:var(--ink);letter-spacing:.2px;white-space:nowrap}
.brand-tagline{position:absolute;left:66px;top:71px;font-size:8px;font-weight:600;color:var(--ink);white-space:nowrap}
.search{position:absolute;left:495px;top:22px;width:66px;height:20px;border:1px solid #cfcfcf;font-size:6.5px;color:#999;padding:5px 0 0 8px}
.search svg{position:absolute;right:6px;top:6px}
.header-phone{position:absolute;left:578px;top:27px;font-size:8px;color:var(--ink);display:flex;align-items:center;gap:6px;white-space:nowrap}
.header-phone b{font-weight:700}
.main-nav{position:absolute;right:60px;top:65px;display:flex;font-size:7.4px;color:var(--ink);white-space:nowrap}
.main-nav span{height:18px;line-height:18px;padding:0 6px;margin-right:8px}
.main-nav span:last-child{margin-right:0;padding-right:0}
.main-nav .active{background:#2a2a2a;color:var(--white);font-weight:700}
.hero{position:absolute;top:97px;left:0;width:698px;height:334px;background:linear-gradient(180deg,#4a3a28 0%,#8a6f4c 35%,#b59c74 65%,#7a6650 100%)}
.hero-caption{position:absolute;left:60px;top:121px;width:244px;height:84px;background:rgba(30,30,30,.72);padding:17px 22px;color:var(--white)}
.hero-caption h1{font-family:"Roboto Condensed",Arial,sans-serif;font-size:13px;font-weight:700;letter-spacing:.2px;white-space:nowrap}
.hero-caption p{font-size:7.4px;line-height:13px;margin-top:7px}
.hero-dots{position:absolute;left:322px;top:293px;display:flex;gap:2px}
.hero-dots i{width:10px;height:10px;border-radius:50%;border:1.5px solid var(--white);display:block}
.hero-dots i.on{background:var(--white);box-shadow:inset 0 0 0 2px #9b8a6e}
.services{position:absolute;top:444px;left:60px;width:578px;height:108px;display:flex}
.service{position:relative;flex:1}
.service .photo{position:absolute;inset:0}
.service .label{position:absolute;left:0;right:0;bottom:0;height:21px;background:rgba(25,25,25,.8);color:var(--white);font-size:7.8px;font-weight:700;line-height:21px;padding-left:10px}
.service .go{position:absolute;right:0;bottom:0;width:21px;height:21px;background:var(--accent);display:flex;align-items:center;justify-content:center}
.categories{position:absolute;top:571px;left:0;width:698px;height:204px;background:var(--band)}
.section-title{position:absolute;left:0;width:698px;text-align:center;font-size:8.4px;font-weight:700;color:var(--ink)}
.section-title::after{content:"";display:block;width:30px;height:1px;background:#bbb;margin:8px auto 0}
.cat-row{position:absolute;top:62px;left:60px;width:578px;display:flex}
.cat{flex:1;text-align:center;border-right:1px solid var(--line);height:118px}
.cat:last-child{border-right:none}
.cat .photo{width:110px;height:82px;margin:4px auto 0}
.cat .name{font-size:9.6px;margin-top:12px;color:var(--ink)}
.arrow{position:absolute}
.products{position:absolute;top:775px;left:0;width:698px;height:282px}
.card-row{position:absolute;top:59px;left:60px;width:578px;display:flex;justify-content:space-between}
.card{width:134px;height:201px;border:1px solid var(--line);text-align:center;position:relative}
.card .photo{width:100px;height:96px;margin:10px auto 0}
.card .desc{font-size:7.8px;line-height:13.5px;margin:15px 14px 0;height:27px;color:var(--text)}
.card .price{font-size:11.4px;font-weight:700;color:var(--price);margin-top:8px}
.card .more{position:absolute;left:-1px;right:-1px;bottom:-1px;height:21px;background:var(--ink);color:var(--white);font-size:7.2px;font-weight:700;display:flex;align-items:center;justify-content:center;gap:6px}
.site-footer{position:absolute;top:1057px;left:0;width:698px;height:143px;background:var(--footer);color:var(--footer-text)}
.footer-title{position:absolute;top:21px;font-size:6.8px;font-weight:700;color:var(--white)}
.contact-list{position:absolute;left:60px;top:45px;font-size:7.4px;line-height:13.5px}
.contact-list li{list-style:none;display:flex;gap:10px;margin-bottom:6px}
.contact-list svg{flex:none;margin-top:3px}
.social{position:absolute;right:60px;top:42px;display:flex;gap:4px}
.social i{display:block;width:22px;height:22px;background:#3a3a3a}
.footer-nav{position:absolute;right:60px;top:95px;font-size:6.8px;color:var(--footer-text);white-space:nowrap}
.copyright{position:absolute;right:60px;top:113px;font-size:6.6px;white-space:nowrap}
</style>
</head>
<body>
<header class="site-header">
  <div class="brand"><span class="brand-square"></span><span class="brand-name">MAPLEWICK HAVEN SUPPLY</span></div>
  <div class="brand-tagline">Packaging • Printing • Distribution</div>
  <div class="search">SEARCH
    <svg width="7" height="7" viewBox="0 0 10 10"><circle cx="4" cy="4" r="3" fill="none" stroke="#999" stroke-width="1.4"/><line x1="6.3" y1="6.3" x2="9.3" y2="9.3" stroke="#999" stroke-width="1.4"/></svg>
  </div>
  <div class="header-phone">
    <svg width="9" height="9" viewBox="0 0 10 10"><path d="M2 0l2 2.5-1.2 1.3a6 6 0 0 0 3.4 3.4L7.5 6 10 8l-1.5 2C4 10 0 6 0 1.5z" fill="#888"/></svg>
    <b>555-318-4620</b>
  </div>
  <nav class="main-nav">
    <span class="active">HOME</span><span>PRODUCTS</span><span>ABOUT US</span><span>LOCATIONS</span><span>NEWS</span><span>CONTACT US</span>
  </nav>
</header>

<section class="hero" role="img" aria-label="Warehouse aisle lined with shelves of cardboard boxes and wooden pallets">
  <div class="hero-caption">
    <h1>LOREM IPSUM IS SIMPLY DUMMY</h1>
    <p>Contrary to popular belief, Lorem Ipsum is not simply random text. It has roots in a piece of classical</p>
  </div>
  <div class="hero-dots"><i class="on"></i><i></i><i></i><i></i></div>
</section>

<section class="services">
  <div class="service">
    <div class="photo" role="img" aria-label="Distribution warehouse with tall blue racks" style="background:linear-gradient(135deg,#8aa1c4,#3c5a8e 60%,#c8ccd4)"></div>
    <div class="label">DISTRIBUTION</div>
    <div class="go"><svg width="6" height="8" viewBox="0 0 6 8"><path d="M1 1l3 3-3 3" fill="none" stroke="#222" stroke-width="1.6"/></svg></div>
  </div>
  <div class="service">
    <div class="photo" role="img" aria-label="Printing press running colourful sheets" style="background:linear-gradient(135deg,#5a6b7d,#3a5f9a 50%,#d2a23a)"></div>
    <div class="label">PRINTING</div>
    <div class="go"><svg width="6" height="8" viewBox="0 0 6 8"><path d="M1 1l3 3-3 3" fill="none" stroke="#222" stroke-width="1.6"/></svg></div>
  </div>
  <div class="service">
    <div class="photo" role="img" aria-label="Hands holding a taped cardboard parcel" style="background:linear-gradient(135deg,#3d5b8a,#b48a5c 55%,#d9bf96)"></div>
    <div class="label">PACKAGING</div>
    <div class="go"><svg width="6" height="8" viewBox="0 0 6 8"><path d="M1 1l3 3-3 3" fill="none" stroke="#222" stroke-width="1.6"/></svg></div>
  </div>
</section>

<section class="categories">
  <h2 class="section-title" style="top:24px">OUR CATEGORIES</h2>
  <svg class="arrow" style="left:30px;top:115px" width="9" height="14" viewBox="0 0 9 14"><path d="M7 1L2 7l5 6" fill="none" stroke="#999" stroke-width="2.4"/></svg>
  <div class="cat-row">
    <div class="cat"><div class="photo" role="img" aria-label="Stack of cardboard boxes" style="background:radial-gradient(ellipse at center,#c89a62 0%,#b7864f 55%,var(--band) 75%)"></div><div class="name">Packaging</div></div>
    <div class="cat"><div class="photo" role="img" aria-label="Incandescent and compact fluorescent light bulbs" style="background:radial-gradient(ellipse at center,#e8e8e8 0%,#c9c9c9 50%,var(--band) 75%)"></div><div class="name">Retail</div></div>
    <div class="cat"><div class="photo" role="img" aria-label="Yellow hard hat with work gloves and tape" style="background:radial-gradient(ellipse at center,#f2c21a 0%,#e0a91a 45%,#4a66a8 62%,var(--band) 78%)"></div><div class="name">Industrial</div></div>
    <div class="cat"><div class="photo" role="img" aria-label="Office supplies with pencils, scissors and stapler" style="background:radial-gradient(ellipse at center,#f6f6f6 0%,#d5d5d5 45%,#c0413a 60%,var(--band) 78%)"></div><div class="name">Office</div></div>
  </div>
  <svg class="arrow" style="left:654px;top:115px" width="9" height="14" viewBox="0 0 9 14"><path d="M2 1l5 6-5 6" fill="none" stroke="#999" stroke-width="2.4"/></svg>
</section>

<section class="products">
  <h2 class="section-title" style="top:21px">OUR PRODUCTS</h2>
  <svg class="arrow" style="left:30px;top:145px" width="9" height="14" viewBox="0 0 9 14"><path d="M7 1L2 7l5 6" fill="none" stroke="#999" stroke-width="2.4"/></svg>
  <div class="card-row">
    <article class="card"><div class="photo" role="img" aria-label="Wooden ruler" style="background:linear-gradient(135deg,#fff 30%,#d9a45a 48%,#c08a42 55%,#fff 72%)"></div><p class="desc">There are many variations of passages</p><p class="price">$8.00</p><div class="more">LEARN MORE</div></article>
    <article class="card"><div class="photo" role="img" aria-label="Blue binder stacked on black binders" style="background:linear-gradient(160deg,#fff 15%,#2a62b8 40%,#1c3f80 60%,#1a1a1a 80%,#fff 92%)"></div><p class="desc">It is a long established fact that a reader.</p><p class="price">$15.00</p><div class="more">LEARN MORE</div></article>
    <article class="card"><div class="photo" role="img" aria-label="Lined notepad with pencils" style="background:linear-gradient(180deg,#fff 5%,#f1f1f1 20%,#e9e9e9 80%,#fff 95%)"></div><p class="desc">There are many variations of passages</p><p class="price">$23.00</p><div class="more">LEARN MORE</div></article>
    <article class="card"><div class="photo" role="img" aria-label="Wooden bar stool" style="background:radial-gradient(ellipse at center,#6b3a1e 0%,#5a2f17 40%,#fff 70%)"></div><p class="desc">Sed ut perspiciatis unde omnis iste natus.</p><p class="price">$11.00</p><div class="more">LEARN MORE</div></article>
  </div>
  <svg class="arrow" style="left:654px;top:145px" width="9" height="14" viewBox="0 0 9 14"><path d="M2 1l5 6-5 6" fill="none" stroke="#999" stroke-width="2.4"/></svg>
</section>

<footer class="site-footer">
  <h3 class="footer-title" style="left:60px">CONTACT US</h3>
  <ul class="contact-list">
    <li><svg width="7" height="9" viewBox="0 0 8 11"><path d="M4 0a4 4 0 0 1 4 4c0 3-4 7-4 7S0 7 0 4a4 4 0 0 1 4-4z" fill="#fff"/><circle cx="4" cy="4" r="1.5" fill="#2b2b2b"/></svg><span>2280 Larkfield Mill Road<br>Cedarbrook, TX 77910</span></li>
    <li><svg width="8" height="8" viewBox="0 0 10 10"><path d="M2 0l2 2.5-1.2 1.3a6 6 0 0 0 3.4 3.4L7.5 6 10 8l-1.5 2C4 10 0 6 0 1.5z" fill="#fff"/></svg><span>555-318-4620</span></li>
    <li><svg width="9" height="7" viewBox="0 0 11 8"><rect x=".6" y=".6" width="9.8" height="6.8" fill="none" stroke="#fff" stroke-width="1.1"/><path d="M.6.6l4.9 4 4.9-4" fill="none" stroke="#fff" stroke-width="1.1"/></svg><span>info@companyname.com</span></li>
  </ul>
  <h3 class="footer-title" style="right:60px">FOLLOW US ON</h3>
  <div class="social"><i></i><i></i><i></i><i></i></div>
  <nav class="footer-nav">HOME &nbsp;|&nbsp; PRODUCTS &nbsp;|&nbsp; ABOUT US &nbsp;|&nbsp; LOCATIONS &nbsp;|&nbsp; NEWS &nbsp;|&nbsp; CONTACT US</nav>
  <p class="copyright">COPYRIGHTS @ 2015 ALL RIGHTS RESERVED</p>
</footer>
</body>
</html>
```